Bref créative
Brochure for Veterinary Acupuncture and Physical Therapy
Willowmere Pet Wellness
Bringing calm to every visit
I am a veterinarian. My business is to travel from between existing veterinary practices to do acupucture and physical therapy with dogs and cats. This brochure will be something for the veterinary clinic to give their client about this service.
Animals
Veterinary pet owners
3 fold brochure
Photos and logo. Text will be coming in a separate upload. I'm not sure how much text is appropriate, so for now, can you put empty text boxes in designs so I can see how it might lay out? One section should be about me (picture of me with the dog), one section about acupuncture and one about physical therapy. Then another text box about how to schedule an appointment.
Me
Physical therapy picture
website: willowmerepetwellness.com
email: willowmerevet@postvale.com
Also needs a plain square
My business card, if that helps
Conditions treated -- depending on space I can shorten the physical therapy information
Overview
This is about me
Scheduling
New "training"
New mission

```html
<!DOCTYPE html>
<html lang="en">
<head>
<meta charset="utf-8">
<title>Willowmere Pet Wellness – Trifold Brochure</title>
<link href="https://fonts.googleapis.com/css2?family=Cinzel:wght@600&family=Lato:wght@400;700&display=swap" rel="stylesheet">
<style>
:root{
  --bg:#e7e1d7;
  --paper:#ffffff;
  --green:#3f9a3c;
  --green-dark:#2f7d31;
  --blue:#2b3f93;
  --blue-light:#4a63b8;
  --ink:#333333;
  --muted:#666666;
}
*{box-sizing:border-box;margin:0;padding:0}
html,body{width:1200px;height:562px;overflow:hidden;background:var(--bg);font-family:'Lato',sans-serif;color:var(--ink)}
.sheet{position:absolute;top:30px;width:564px;height:500px;background:var(--paper);display:flex;box-shadow:0 2px 8px rgba(0,0,0,.18);overflow:hidden}
.sheet--outside{left:24px}
.sheet--inside{left:612px}
.panel{position:relative;width:188px;height:100%;overflow:hidden}
.panel + .panel{border-left:1px solid #eee}
.photo{position:absolute;display:block}
.heading{font-family:'Cinzel',serif;font-weight:600;color:var(--green);font-size:12px;line-height:1.2}
.body{font-size:6.2px;line-height:1.5;color:var(--muted)}
.logo{display:flex;align-items:center;gap:6px}
.logo__mark{width:16px;height:16px;border-radius:50%;background:var(--green);flex:none}
.logo__name{font-family:'Lato',sans-serif;font-weight:700;color:var(--green);font-size:13px;line-height:1.1}
.list{list-style:none;font-size:6.2px;line-height:1.55}
.list li::before{content:"• ";color:var(--green)}

/* outside: about */
.about .photo{left:0;top:0;width:188px;height:225px;background:linear-gradient(160deg,#c9b08d,#8e7656 60%,#5d6f3c)}
.about .heading{position:absolute;left:14px;top:240px}
.about .body{position:absolute;left:14px;top:262px;width:160px}

/* outside: scheduling */
.schedule .band{position:absolute;left:0;top:0;width:188px;height:150px;background:var(--blue)}
.schedule .photo{left:52px;top:24px;width:84px;height:100px;background:linear-gradient(170deg,#d6c3a4,#8a7458)}
.schedule .green{position:absolute;left:0;top:150px;width:188px;height:10px;background:var(--green)}
.schedule .heading{position:absolute;left:14px;top:176px;color:var(--blue);font-size:11px}
.schedule .body{position:absolute;left:14px;top:196px;width:160px}
.schedule .call{position:absolute;left:14px;top:268px;width:160px;font-size:8px;font-weight:700;color:var(--green);line-height:1.35}
.contact{position:absolute;left:14px;top:320px;list-style:none;font-size:7px;line-height:2.1;color:var(--ink)}
.contact li{display:flex;align-items:center;gap:5px}
.contact .sq{width:8px;height:8px;background:var(--blue);display:inline-block}

/* outside: cover */
.cover .logo{position:absolute;left:16px;top:70px;width:160px}
.cover .rule{position:absolute;left:16px;top:112px;width:156px;height:2px;background:var(--blue)}
.cover .photo{left:0;top:130px;width:188px;height:280px;background:linear-gradient(160deg,#b89b79,#6e5a45 55%,#3b3029)}
.cover .url{position:absolute;left:0;bottom:40px;width:188px;text-align:center;font-size:9px;color:var(--blue)}

/* inside: overview */
.overview .body{position:absolute;left:14px;top:20px;width:160px}
.overview .photo{left:14px;top:250px;width:160px;height:180px;background:linear-gradient(160deg,#5b4a3b,#2e2520 50%,#4f6fa8)}

/* inside: acupuncture */
.acu .photo{left:0;top:0;width:188px;height:150px;background:linear-gradient(170deg,#c4b39c,#7c6a58)}
.acu .heading{position:absolute;left:14px;top:160px;font-size:11px}
.acu .box{position:absolute;left:0;top:196px;width:188px;height:244px;background:var(--green);padding:14px}
.acu .box .heading{position:static;color:#fff;font-size:11px;margin-bottom:8px}
.acu .box .list{color:#fff}
.acu .box .list li::before{color:#fff}

/* inside: physical therapy */
.pt .photo{left:0;top:0;width:188px;height:120px;background:linear-gradient(170deg,#9fc6e6,#4f87c2 55%,#3a5d8f)}
.pt .heading{position:absolute;left:14px;top:130px;width:164px;font-size:10.5px;color:var(--blue)}
.pt .list{position:absolute;left:14px;top:168px;width:164px}
.pt .call{position:absolute;left:14px;top:392px;width:164px;font-size:7px;font-weight:700;color:var(--green)}

.tagline-band{position:absolute;left:188px;bottom:0;width:376px;height:60px}
.tagline-band .stripe{position:absolute;left:0;top:0;width:100%;height:6px;background:var(--green)}
.tagline-band .bar{position:absolute;left:0;top:6px;width:100%;height:54px;background:var(--blue);display:flex;align-items:center;justify-content:center}
.tagline{font-family:'Cinzel',serif;font-weight:600;color:#fff;font-size:12px;letter-spacing:1.5px;text-transform:uppercase}
</style>
</head>
<body>

<section class="sheet sheet--outside">
  <div class="panel about">
    <div class="photo" role="img" aria-label="Photo of the veterinarian with her dog"></div>
    <h2 class="heading">About the Doctor</h2>
    <p class="body">Dr. Kessa earned her veterinary degree in 2004 and has practiced small animal medicine ever since. She holds certification in veterinary acupuncture and canine rehabilitation therapy. Today she travels between partner clinics, bringing gentle hands-on care to dogs and cats of every age. Her goal is to help each patient move with less pain, recover faster after surgery or injury, and enjoy a better quality of life at home with the family that loves them.</p>
  </div>

  <div class="panel schedule">
    <div class="band"></div>
    <div class="photo" role="img" aria-label="Photo of a small dog"></div>
    <div class="green"></div>
    <h2 class="heading">Scheduling an appointment</h2>
    <p class="body">Appointments are held at your own veterinary clinic. Your veterinarian will review the history and send a referral so that the first visit can focus on a full exam and a care plan.</p>
    <p class="call">Please call your veterinarian for the referral.</p>
    <ul class="contact">
      <li><span class="sq"></span>willowmerevet@postvale.com</li>
      <li><span class="sq"></span>WillowmerePetWellness</li>
      <li><span class="sq"></span>drkessa · tovique</li>
    </ul>
  </div>

  <div class="panel cover">
    <div class="logo">
      <span class="logo__mark"></span>
      <span class="logo__name">Willowmere Pet Wellness</span>
    </div>
    <div class="rule"></div>
    <div class="photo" role="img" aria-label="Photo of a dog resting at home"></div>
    <p class="url">willowmerepetwellness.com</p>
  </div>
</section>

<section class="sheet sheet--inside">
  <div class="panel overview">
    <p class="body">Acupuncture is an ancient practice that places fine needles at specific points on the body. It gently stimulates nerves, improves blood flow and releases natural pain relief. Most pets relax quickly during treatment, and many fall asleep. Sessions last about thirty minutes and are scheduled weekly at first.<br><br>Physical therapy uses exercise, stretching, massage and underwater treadmill work to rebuild strength and mobility. A plan is made for each patient and shared with the family for home care between visits.</p>
    <div class="photo" role="img" aria-label="Photo of a dog resting on a bed during treatment"></div>
  </div>

  <div class="panel acu">
    <div class="photo" role="img" aria-label="Photo of a dog receiving acupuncture"></div>
    <h2 class="heading">Veterinary acupuncture can treat:</h2>
    <div class="box">
      <h3 class="heading">Conditions Commonly Treated with Acupuncture</h3>
      <ul class="list">
        <li>Arthritis and joint pain</li>
        <li>Back and neck disease</li>
        <li>Nerve injury and weakness</li>
        <li>Digestive upset</li>
        <li>Skin and allergy issues</li>
        <li>Anxiety and stress</li>
        <li>Recovery after surgery</li>
      </ul>
    </div>
  </div>

  <div class="panel pt">
    <div class="photo" role="img" aria-label="Photo of a dog on an underwater treadmill"></div>
    <h2 class="heading">Veterinary physical therapy and rehabilitation can treat:</h2>
    <ul class="list">
      <li>Cruciate ligament repair</li>
      <li>Hip and elbow dysplasia</li>
      <li>Spinal surgery recovery</li>
      <li>Muscle loss and weakness</li>
      <li>Weight management</li>
      <li>Senior mobility decline</li>
      <li>Sports and working dogs</li>
      <li>Fracture recovery</li>
    </ul>
    <p class="call">Please call your veterinarian today.</p>
  </div>

  <div class="tagline-band">
    <div class="stripe"></div>
    <div class="bar"><span class="tagline">Bringing calm to every visit</span></div>
  </div>
</section>

</body>
</html>
```